Maple Roster Business Card for recruitment company

We are looking for a Business Card Design that incorporates our personal details and our busines name and logo. We are a specialized search consultancy that recruit Property and Construction professionals.
We would like a business card that stands out and is appealing to the Construction and Property industry as well.

Target Market(s)

people in the construction and property industry

Contact Information for Business Card

Business Name and logo

Font styles to use
Serif

Colors
0094D4
00A9DD
6FCCEA
C7EBF8
E9F6FB

Requirements
Must have
• Business name and logo as well as contact details
Should not have
• No photos of us please

```html
<!DOCTYPE html>
<html lang="en">
<head>
<meta charset="utf-8">
<title>Maple Roster Business Card</title>
<link rel="stylesheet" href="https://fonts.googleapis.com/css2?family=Lato:wght@300;400;700&display=swap">
<style>
  :root {
    --bg: #e4e4e4;
    --card: #ffffff;
    --teal: #0d5a6c;
    --navy: #0b3a4d;
    --ink: #444a4e;
    --ink-dark: #1f2a30;
    --grey-band: #a3a3a3;
    --back-dark: #002e3e;
    --back-light: #006a7d;
    --white: #ffffff;
  }
  * { margin: 0; padding: 0; box-sizing: border-box; }
  html, body { width: 1200px; height: 1200px; overflow: hidden; }
  body {
    background: var(--bg);
    font-family: "Lato", sans-serif;
    position: relative;
  }
  .card {
    position: absolute;
    left: 257px;
    width: 686px;
    height: 392px;
    box-shadow: 0 14px 30px rgba(0,0,0,0.18);
    overflow: hidden;
  }
  .card-front { top: 165px; background: var(--card); }
  .card-back {
    top: 653px;
    background: linear-gradient(30deg, var(--back-dark) 0%, #014b5e 55%, var(--back-light) 100%);
  }
  .brand-name {
    position: absolute;
    right: 50px;
    top: 62px;
    font-size: 45px;
    font-weight: 400;
    letter-spacing: 1px;
    color: var(--teal);
    line-height: 1;
    text-transform: uppercase;
  }
  .person { position: absolute; left: 40px; top: 210px; }
  .person-name {
    font-size: 25px;
    font-weight: 700;
    color: var(--navy);
    line-height: 1;
    text-transform: uppercase;
  }
  .person-title {
    font-size: 16px;
    color: var(--ink-dark);
    margin-top: 3px;
  }
  .divider {
    position: absolute;
    left: 40px;
    right: 48px;
    top: 261px;
    border-top: 1.5px dashed var(--navy);
  }
  .contact-list {
    position: absolute;
    left: 40px;
    top: 272px;
    list-style: none;
    font-size: 15.5px;
    color: var(--ink);
    line-height: 19.6px;
  }
  .contact-list li { display: flex; align-items: center; }
  .contact-list svg { width: 13px; height: 13px; margin-right: 10px; fill: var(--navy); }
  .address {
    position: absolute;
    right: 50px;
    top: 272px;
    text-align: right;
    font-size: 15.5px;
    color: var(--ink);
    line-height: 19.6px;
  }
  .address .web { color: var(--teal); }
  .band { position: absolute; bottom: 0; height: 11px; }
  .band-dark { left: 0; width: 450px; background: var(--navy); clip-path: polygon(0 0, 100% 0, calc(100% - 4px) 100%, 0 100%); }
  .band-grey { right: 0; width: 232px; background: var(--grey-band); clip-path: polygon(4px 0, 100% 0, 100% 100%, 0 100%); }
  .back-brand {
    position: absolute;
    left: 0; right: 0;
    top: 150px;
    display: flex;
    justify-content: center;
    align-items: center;
    gap: 14px;
  }
  .back-brand .dot {
    width: 22px; height: 22px;
    border-radius: 50%;
    background: var(--white);
  }
  .back-brand .word {
    font-size: 40px;
    font-weight: 400;
    letter-spacing: 2px;
    color: var(--white);
    text-transform: uppercase;
  }
  .back-web {
    position: absolute;
    left: 0; right: 0;
    top: 336px;
    text-align: center;
    font-size: 16px;
    letter-spacing: 6px;
    color: var(--white);
    text-transform: uppercase;
  }
</style>
</head>
<body>
  <section class="card card-front">
    <div class="brand-name">Maple Roster</div>
    <div class="person">
      <div class="person-name">Daniel Harper</div>
      <div class="person-title">President</div>
    </div>
    <div class="divider"></div>
    <ul class="contact-list">
      <li><svg viewBox="0 0 16 16"><path d="M3.5 1l3 3-1.6 2.2c.9 1.8 2.2 3.1 4 4L11.1 8.6l3 3L12.5 14C6.7 14 2 9.3 2 3.5z"/></svg>555-214-7390</li>
      <li><svg viewBox="0 0 16 16"><path d="M4 0h8a1 1 0 011 1v14a1 1 0 01-1 1H4a1 1 0 01-1-1V1a1 1 0 011-1zm1 2v10h6V2z"/></svg>555-318-6042</li>
      <li><svg viewBox="0 0 16 16"><path d="M4 1h8v4H4zM1 6h14v6h-3v3H4v-3H1zm4 4v3h6v-3z"/></svg>555-427-1856</li>
      <li><svg viewBox="0 0 16 16"><path d="M1 3h14v10H1zm1.5 1.5L8 9l5.5-4.5v-.1h-11z"/></svg>daniel@mapleroster.com</li>
    </ul>
    <div class="address">
      Maple Roster Group<br>
      4120 Birchwood Avenue<br>
      Portland, Oregon 97204<br>
      <span class="web">www.mapleroster.com</span>
    </div>
    <div class="band band-dark"></div>
    <div class="band band-grey"></div>
  </section>

  <section class="card card-back">
    <div class="back-brand">
      <span class="dot"></span>
      <span class="word">Maple Roster</span>
    </div>
    <div class="back-web">www.mapleroster.com</div>
  </section>
</body>
</html>
```